Mailer 001

https://www.filetrove.example/sh/xk29pq7rlm04vbz/4hTzcRwqPn
Orentation: Landscape
SIZE: 5 1/2' by 10 1/2'
COLORS: 32cd32, 13e613, 21f721, 00FE00, 00D800, 00B200, 009900

Re-Elect Darren Holcomb
Utah House of Representatives
Questions? Please call! (801) 555-0147

Text for side 1

Promises Made - Promises Kept
- Again I Promise to continue to advocate for limited government
- Again I Promise to advocate for educational choice
- Again I Promise to promote fiscal responsibility, transparency, and accountability.
- Again I Promise to take seriously my pledge to protect individual and economic liberty.

Text for side 2

Principled Conservative
I am committed to my oath to uphold the U.S. Constitution and Utah Constitution. As an attorney who has studied these documents, I understand the principles of federalism and of our republican form of government. I also understand that big government is a threat to our freedoms, even at the state and local levels. I have a record of sponsoring and supporting legislation that makes government more efficient and less burdensome.
- Darren Holcomb

Let’s finish what WE started
www.DarrenHolcombLD57.example

Note: side 2 needs room for address lables as this will be a mailer sent out in the US post
, This is a mailer for a client of mine. It will be mailed out soon.
There is a filetrove link so you can look at some of the work done previously, the work done before was not done by a professional, but it will give you an idea of the branding style. Colors should match previous branding.

feel free to ask questions if needed.

Filetrove: https://www.filetrove.example/sh/xk29pq7rlm04vbz/4hTzcRwqPn
Orientation: Landscape
SIZE: 5 1/2' by 10 1/2'

Re-Elect Darren Holcomb

Text for side 1

Text for side 2

Principled Conservative
- Darren Holcomb

www.DarrenHolcombLD57.example

Updates

If you are unable to get to the filetrove you and download a zip file.
https://docs.storvault.example/file/d/3Kq8ZmTyW1pR5LxNvc2HbJsDfgQe/edit?usp=sharing

Please note: we are looking for fresh and creative designs, not designs that look like the old flyers done by non-professionals.

Make the designs fresh and creative, I know that is an old a tired bit of instructions and ambiguous, so to clear that up a bit.....if the design look like I could have knocked I personally could have done, that is not what I want.  Do not just cut and paste images, use transparency, complementary colors and fading.  The design should be artistic.

bring your creativity and artistic nature.

```html
<!DOCTYPE html>
<html lang="en">
<head>
<meta charset="utf-8">
<title>Re-Elect Darren Holcomb – Mailer</title>
<link rel="stylesheet" href="https://fonts.googleapis.com/css2?family=Marcellus&family=Merriweather:wght@700&family=Source+Sans+3:wght@400;600;700&family=Caveat:wght@500&display=swap">
<style>
  :root {
    --backdrop: #3f322a;
    --campaign-green: #4cb748;
    --headline-red: #e1202f;
    --bullet-red: #c8202a;
    --reelect-red: #7a1b1b;
    --navy: #17406a;
    --ink: #1d2a1d;
    --slogan-ink: #13210f;
    --paper: #ffffff;
    --paper-shade: #e4e6e8;
    --silver-light: #f4f4f4;
    --silver-dark: #8d8f92;
  }
  * { box-sizing: border-box; margin: 0; padding: 0; }
  html, body { width: 1151px; height: 1200px; overflow: hidden; }
  body { background: var(--backdrop); position: relative; font-family: "Source Sans 3", sans-serif; }

  .mailer-side {
    position: absolute; left: 137px; width: 866px; height: 453px;
    background: linear-gradient(180deg, var(--paper) 0%, var(--paper-shade) 100%);
    overflow: hidden; box-shadow: 0 8px 22px rgba(0,0,0,.45);
  }
  .side-front { top: 107px; }
  .side-back { top: 616px; background: linear-gradient(90deg, var(--paper-shade), var(--paper) 60%, var(--paper-shade)); }
  .curve-art { position: absolute; inset: 0; }

  .candidate-photo {
    position: absolute; left: 0; top: 88px; width: 440px; height: 365px;
    background: linear-gradient(180deg, #eef0f3 0%, #c9ced8 35%, #8a6a5c 62%, #5a3a33 100%);
  }

  /* Front headline */
  .headline {
    position: absolute; font-family: "Marcellus", serif; color: var(--headline-red);
    font-size: 50px; line-height: 1; font-weight: 400;
    transform: scaleX(.7); transform-origin: left top; white-space: nowrap;
  }
  .headline-made { left: 32px; top: 30px; }
  .headline-kept { left: 177px; top: 82px; }

  /* Campaign name block */
  .ballot-mark { position: absolute; }
  .ballot-mark .name-top { display: flex; justify-content: space-between; align-items: flex-end; }
  .ballot-mark .reelect { font-family: "Marcellus", serif; color: var(--reelect-red); }
  .ballot-mark .first-name,
  .ballot-mark .last-name { font-family: "Marcellus", serif; color: var(--paper); line-height: 1; }
  .ballot-mark .last-name { display: block; text-align: center; }
  .ballot-mark .office-row { display: flex; align-items: center; white-space: nowrap; }
  .ballot-mark .office-dot { border-radius: 50%; background: var(--navy); flex: none; }
  .ballot-mark .office { font-family: "Marcellus", serif; color: var(--ink); }
  .ballot-mark .tagline {
    background: var(--navy); color: var(--paper); font-family: "Marcellus", serif; text-align: center;
  }
  .ballot-mark .site { color: var(--ink); text-align: center; line-height: 1; }

  .front-mark { left: 602px; top: 30px; width: 236px; }
  .front-mark .name-top { height: 34px; margin-top: 4px; padding-left: 14px; }
  .front-mark .reelect { font-size: 18px; line-height: 22px; }
  .front-mark .first-name { font-size: 30px; }
  .front-mark .last-name { font-size: 54px; height: 58px; line-height: 58px; }
  .front-mark .office-row { margin-top: 4px; height: 18px; padding-left: 14px; gap: 8px; }
  .front-mark .office-dot { width: 14px; height: 14px; }
  .front-mark .office { font-size: 14px; }
  .front-mark .tagline { margin-top: 10px; height: 30px; font-size: 19px; line-height: 30px; }
  .front-mark .site { font-size: 6px; margin-top: 4px; }

  /* Front promises */
  .promise-list { position: absolute; left: 456px; top: 250px; width: 400px; list-style: none; }
  .promise-list li {
    position: relative; padding-left: 20px; color: var(--paper);
    font-weight: 700; font-size: 14.5px; line-height: 21px; margin-bottom: 8px;
    text-shadow: 0 1px 1px rgba(0,0,0,.25);
  }
  .promise-list li::before {
    content: ""; position: absolute; left: 0; top: 4px; width: 13px; height: 13px;
    border-radius: 50%; background: var(--bullet-red); border: 2px solid var(--paper);
  }

  /* Back message */
  .back-title {
    position: absolute; left: 36px; top: 26px; color: var(--paper); white-space: nowrap;
    font-family: "Merriweather", serif; font-weight: 700; font-size: 28px; line-height: 1.3;
  }
  .back-quote {
    position: absolute; left: 36px; top: 104px; width: 330px;
    color: var(--paper); font-size: 14px; line-height: 19.3px; text-align: justify;
  }
  .back-attribution {
    position: absolute; left: 36px; top: 281px; width: 330px; text-align: right;
    color: var(--paper); font-size: 16px; line-height: 20px;
  }
  .back-slogan {
    position: absolute; left: 36px; top: 342px; color: var(--slogan-ink); white-space: nowrap;
    font-family: "Caveat", cursive; font-size: 33px; line-height: 40px;
  }
  .back-url {
    position: absolute; left: 36px; top: 395px; color: var(--paper); white-space: nowrap;
    font-family: "Merriweather", serif; font-weight: 700; font-size: 17.5px; line-height: 26px; letter-spacing: .3px;
  }

  /* Back address panel */
  .back-mark {
    left: 508px; top: 37px; width: 178px; height: 134px; background: var(--campaign-green);
    border-radius: 6px; padding: 4px 9px;
  }
  .back-mark .name-top { height: 26px; padding-left: 2px; }
  .back-mark .reelect { font-size: 13px; line-height: 16px; }
  .back-mark .first-name { font-size: 22px; }
  .back-mark .last-name { font-size: 40px; height: 42px; line-height: 42px; }
  .back-mark .office-row { margin-top: 3px; height: 14px; gap: 5px; }
  .back-mark .office-dot { width: 10px; height: 10px; }
  .back-mark .office { font-size: 10px; }
  .back-mark .tagline { margin-top: 5px; height: 22px; font-size: 14px; line-height: 22px; }
  .back-mark .site { font-size: 5px; margin-top: 3px; }

  .stamp-box {
    position: absolute; left: 703px; top: 37px; width: 120px; height: 134px;
    border: 1.5px solid #333; border-radius: 8px; background: var(--paper);
  }
  .address-to { position: absolute; left: 494px; top: 254px; font-size: 15px; line-height: 20px; color: #444; }
  .address-line { position: absolute; left: 508px; width: 315px; height: 1px; background: #888; }
  .line-1 { top: 281px; }
  .line-2 { top: 327px; }
  .line-3 { top: 370px; }
  .line-4 { top: 414px; }
</style>
</head>
<body>

<section class="mailer-side side-front">
  <div class="candidate-photo" role="img" aria-label="Photo of the candidate in a blue shirt and striped tie, arms crossed, in front of a mountain range"></div>
  <svg class="curve-art" viewBox="0 0 866 453" aria-hidden="true">
    <defs>
      <linearGradient id="silverFront" x1="0" x2="1">
        <stop offset="0" stop-color="#8d8f92"/>
        <stop offset=".5" stop-color="#f4f4f4"/>
        <stop offset="1" stop-color="#8d8f92"/>
      </linearGradient>
    </defs>
    <path d="M 404 0 C 470 120, 472 300, 384 453" fill="none" stroke="url(#silverFront)" stroke-width="16"/>
    <path d="M 418 0 C 484 120, 486 300, 398 453 L 866 453 L 866 0 Z" fill="#4cb748"/>
  </svg>

  <h1 class="headline headline-made">PROMISES MADE</h1>
  <h1 class="headline headline-kept">PROMISES KEPT</h1>

  <div class="ballot-mark front-mark">
    <div class="name-top"><span class="reelect">Re-Elect</span><span class="first-name">Darren</span></div>
    <span class="last-name">Holcomb</span>
    <div class="office-row"><span class="office-dot"></span><span class="office">Utah House of Representatives</span></div>
    <div class="tagline">principled conservative</div>
    <div class="site">voteholcomb.example</div>
  </div>

  <ul class="promise-list">
    <li>Again I Promise to continue to advocate<br>for limited government</li>
    <li>Again I Promise to advocate for educational choice</li>
    <li>Again I Promise to promote fiscal responsibility,<br>transparency, and accountability.</li>
    <li>Again I Promise to take seriously my pledge to<br>protect individual and economic liberty.</li>
  </ul>
</section>

<section class="mailer-side side-back">
  <svg class="curve-art" viewBox="0 0 866 453" aria-hidden="true">
    <defs>
      <linearGradient id="silverBack" x1="0" x2="1">
        <stop offset="0" stop-color="#8d8f92"/>
        <stop offset=".5" stop-color="#f4f4f4"/>
        <stop offset="1" stop-color="#8d8f92"/>
      </linearGradient>
    </defs>
    <path d="M 474 0 C 422 90, 407 200, 407 453" fill="none" stroke="url(#silverBack)" stroke-width="16"/>
    <path d="M 0 0 L 462 0 C 410 90, 395 200, 395 453 L 0 453 Z" fill="#4cb748"/>
  </svg>

  <h2 class="back-title">Principled Conservative</h2>
  <p class="back-quote">“ I am committed to my oath to uphold the U.S. Constitution and Utah Constitution. As an attorney who has studied these documents, I understand the principles of federalism and of our republican form of government. I also understand that big government is a threat to our freedoms, even at the state and local levels. I have a record of sponsoring and supporting legislation that makes government more efficient and less burdensome. ”</p>
  <p class="back-attribution">- Darren Holcomb</p>
  <p class="back-slogan">Let’s finish what WE started</p>
  <p class="back-url">www.DarrenHolcombLD57.example</p>

  <div class="ballot-mark back-mark">
    <div class="name-top"><span class="reelect">Re-Elect</span><span class="first-name">Darren</span></div>
    <span class="last-name">Holcomb</span>
    <div class="office-row"><span class="office-dot"></span><span class="office">Utah House of Representatives</span></div>
    <div class="tagline">principled conservative</div>
    <div class="site">voteholcomb.example</div>
  </div>

  <div class="stamp-box"></div>
  <p class="address-to">To,</p>
  <div class="address-line line-1"></div>
  <div class="address-line line-2"></div>
  <div class="address-line line-3"></div>
  <div class="address-line line-4"></div>
</section>

</body>
</html>
```